Income Tax Flyer - Updates Needed

Just need to update this flyer design and give it a new look. We would like to keep all the same wording but make it stand out a little more. Our selling point is the "Same Day Tax Advance up to $6,000"

Lending, Small Loans, Tax Services, Title Loans, Personal Loans

```html
<!DOCTYPE html>
<html lang="en">
<head>
<meta charset="UTF-8">
<title>Same Day Tax Advance – Crestline Financial Group</title>
<link rel="stylesheet" href="https://fonts.googleapis.com/css2?family=Poppins:wght@500;600;700;800&display=swap">
<style>
  :root {
    --green-dark: #2c5130;
    --green-mid: #3b6a40;
    --red: #a8232b;
    --badge-grey: #e8e8ea;
    --white: #ffffff;
    --photo-light: #e6ecef;
    --photo-mid: #b9c6cf;
    --photo-deep: #5c6b78;
  }
  * { margin: 0; padding: 0; box-sizing: border-box; }
  html, body { width: 860px; height: 1200px; overflow: hidden; background: var(--white); }
  .flyer {
    position: relative;
    width: 860px;
    height: 1200px;
    overflow: hidden;
    background: var(--white);
    font-family: "Poppins", sans-serif;
    color: var(--green-dark);
  }
  .hero-art, .footer-bands { position: absolute; left: 0; width: 860px; }
  .hero-art { top: 0; height: 620px; }
  .footer-bands { top: 960px; height: 240px; }

  .brand-badge { position: absolute; left: 480px; top: 270px; width: 315px; height: 325px; }
  .brand-name {
    position: absolute;
    left: 492px; top: 398px; width: 290px;
    text-align: center;
    font-weight: 600;
    color: var(--green-dark);
    font-size: 27px;
    line-height: 1.15;
  }
  .brand-name small { display: block; font-size: 13px; letter-spacing: 3px; font-weight: 600; }

  .headline {
    position: absolute; top: 602px; left: 0; width: 860px;
    text-align: center;
    font-weight: 800; font-size: 41px; letter-spacing: -0.5px;
    color: var(--green-dark);
  }
  .amount-box {
    position: absolute; left: 151px; top: 660px; width: 552px; height: 75px;
    background: var(--green-dark);
    color: var(--white);
    font-weight: 700; font-size: 62px; letter-spacing: 2px;
    display: flex; align-items: center; justify-content: center;
  }
  .tagline {
    position: absolute; top: 758px; left: 0; width: 860px;
    text-align: center;
    font-weight: 500; font-size: 25px;
    color: var(--green-dark);
  }
  .tagline strong { color: var(--red); font-weight: 700; font-size: 33px; }

  .features { position: absolute; left: 115px; top: 840px; list-style: none; }
  .feature { display: flex; align-items: center; height: 56px; margin-bottom: 27px; }
  .feature-icon { width: 58px; height: 58px; flex: none; }
  .feature-text { margin-left: 20px; font-size: 19px; font-weight: 500; line-height: 1.25; }

  .divider { position: absolute; left: 432px; top: 835px; width: 1.5px; height: 235px; background: var(--red); }

  .contact { position: absolute; left: 500px; top: 838px; }
  .contact-title { font-size: 27px; font-weight: 600; color: var(--red); margin-bottom: 30px; }
  .contact-phone { font-size: 19px; font-weight: 600; margin-bottom: 12px; }
  .contact-line { font-size: 17px; font-weight: 600; margin-bottom: 11px; }
</style>
</head>
<body>
<main class="flyer">
  <svg class="hero-art" viewBox="0 0 860 620" aria-hidden="false">
    <defs>
      <linearGradient id="photoTone" x1="0" y1="0" x2="1" y2="1">
        <stop offset="0" stop-color="var(--photo-light)"/>
        <stop offset="0.55" stop-color="var(--photo-mid)"/>
        <stop offset="1" stop-color="var(--photo-deep)"/>
      </linearGradient>
    </defs>
    <rect role="img" aria-label="Photo of a smiling couple meeting a financial advisor at an office table" x="0" y="0" width="860" height="620" fill="url(#photoTone)"/>
    <path d="M0,424 L420,535 Q480,552 520,520 L860,170 L860,620 L0,620 Z" fill="var(--red)"/>
    <path d="M0,446 L420,556 Q486,572 530,540 L860,205 L860,620 L0,620 Z" fill="var(--green-mid)"/>
    <path d="M0,468 L420,574 Q492,590 540,556 L860,228 L860,620 L0,620 Z" fill="var(--green-dark)"/>
    <path d="M0,519 L420,594 Q505,606 548,566 L860,238 L860,620 L0,620 Z" fill="var(--white)"/>
  </svg>

  <svg class="brand-badge" viewBox="0 0 315 325" aria-hidden="true">
    <path d="M203,10 Q212,8 220,16 L300,110 Q307,118 305,128 L275,256 Q272,266 262,269 L135,311 Q125,314 118,307 L20,206 Q12,198 15,188 L40,70 Q43,60 53,57 Z" fill="var(--badge-grey)"/>
    <path d="M203,25 L290,125 L262,252 L135,296 L28,195 L55,72 Z" fill="none" stroke="var(--green-dark)" stroke-width="3" stroke-linejoin="round"/>
  </svg>
  <p class="brand-name">Crestline<small>FINANCIAL GROUP</small></p>

  <h1 class="headline">SAME DAY TAX ADVANCE</h1>
  <p class="amount-box">UP TO $6,000</p>
  <p class="tagline">File your tax and apply for an <strong>Easy Advance!</strong></p>

  <ul class="features">
    <li class="feature">
      <svg class="feature-icon" viewBox="0 0 58 58" aria-hidden="true">
        <circle cx="29" cy="29" r="27" fill="none" stroke="var(--red)" stroke-width="1.5"/>
        <circle cx="29" cy="31" r="13" fill="none" stroke="var(--green-dark)" stroke-width="2"/>
        <rect x="26" y="13" width="6" height="4" fill="var(--green-dark)"/>
        <text x="29" y="36" text-anchor="middle" font-family="Poppins, sans-serif" font-size="14" font-weight="700" fill="var(--green-dark)">$</text>
      </svg>
      <span class="feature-text">Available in<br>24 Hours or Less</span>
    </li>
    <li class="feature">
      <svg class="feature-icon" viewBox="0 0 58 58" aria-hidden="true">
        <circle cx="29" cy="29" r="27" fill="none" stroke="var(--red)" stroke-width="1.5"/>
        <circle cx="25" cy="25" r="11" fill="none" stroke="var(--green-dark)" stroke-width="2"/>
        <text x="25" y="30" text-anchor="middle" font-family="Poppins, sans-serif" font-size="13" font-weight="700" fill="var(--green-dark)">$</text>
        <path d="M31,30 L31,44 M31,36 L40,36 Q44,37 43,42 L41,46" fill="none" stroke="var(--green-dark)" stroke-width="2" stroke-linecap="round"/>
      </svg>
      <span class="feature-text">Choose Your<br>Loan Amount</span>
    </li>
    <li class="feature">
      <svg class="feature-icon" viewBox="0 0 58 58" aria-hidden="true">
        <circle cx="29" cy="29" r="27" fill="none" stroke="var(--red)" stroke-width="1.5"/>
        <rect x="23" y="12" width="18" height="28" rx="2" fill="none" stroke="var(--green-dark)" stroke-width="2"/>
        <text x="32" y="31" text-anchor="middle" font-family="Poppins, sans-serif" font-size="12" font-weight="700" fill="var(--green-dark)">$</text>
        <path d="M14,38 L22,30 L30,38 L24,46 Z" fill="none" stroke="var(--green-dark)" stroke-width="2" stroke-linejoin="round"/>
      </svg>
      <span class="feature-text">Quick and Easy</span>
    </li>
  </ul>

  <div class="divider"></div>

  <section class="contact">
    <h2 class="contact-title">Contact Us Today!</h2>
    <p class="contact-phone">Phone Number</p>
    <p class="contact-line">Address line 1</p>
    <p class="contact-line">Address line 2</p>
    <p class="contact-line">Address line 3</p>
  </section>

  <svg class="footer-bands" viewBox="0 960 860 240" aria-hidden="true">
    <path d="M0,1074 L640,1128 Q700,1134 742,1094 L860,978 L860,1200 L0,1200 Z" fill="var(--red)"/>
    <path d="M0,1098 L660,1140 Q722,1144 762,1106 L860,1005 L860,1200 L0,1200 Z" fill="var(--green-mid)"/>
    <path d="M0,1120 L680,1150 Q742,1154 782,1114 L860,1036 L860,1200 L0,1200 Z" fill="var(--green-dark)"/>
  </svg>
</main>
</body>
</html>
```